Hartwell Estates Business Cards

I would like a business card that includes myself and my partner.
Includes: Logo, office #, email, website, our names, our numbers and possibly the address. I would also like the logo to be embossed and the card to be horizontal.
There is a photo of our yard signs to give you an idea of the colors of our business.

Target Market(s)

Everyone in real estate market.
We are in a rural area. Our clientele are from all socioeconomic backgrounds.

Industry/Entity Type

Real Estate Agent

Contact Information for Business Card

Company Name: Hartwell Estates
Our Names, Titles & Cell #'s : Dana Pembrook-Broker (555).317.6624, Marla Pembrook-Realtor (555).609.1385
Office #: (555).240.3918
Website: hartwellestates-demo.com
Joint Email: pembrook@hartwellestates-demo.com
Office Address: 418B W. Calloway Ave.
Ashmere Vale, NW. 70913

Font styles to use
Serif

Requirements
Must have
• HORIZONTAL, Logo, Myself and my partners names, Our cell #'s, our office #, our website, our email address
Nice to have
• Embossed logo, office address, our titles.

```html
<!DOCTYPE html>
<html lang="en">
<head>
<meta charset="utf-8">
<title>Hartwell Estates Business Cards</title>
<link href="https://fonts.googleapis.com/css2?family=EB+Garamond:wght@600&family=Source+Sans+3:wght@400;600&display=swap" rel="stylesheet">
<style>
  :root {
    --stage: #000000;
    --card-back: #f3f3f3;
    --card-front: #ffffff;
    --brand: #3d1a5b;
    --ink: #2b2b2b;
  }
  * { margin: 0; padding: 0; box-sizing: border-box; }
  html, body {
    width: 1200px; height: 900px; overflow: hidden;
    background: var(--stage);
  }
  .canvas { position: relative; width: 1200px; height: 900px; }
  .card {
    position: absolute; top: 271px;
    width: 457px; height: 281px;
    border-radius: 12px;
  }
  .card--details { left: 137px; background: var(--card-back); }
  .card--brand { left: 626px; background: var(--card-front); }

  .contacts {
    position: absolute; left: 33px; top: 34px;
    font-family: "Source Sans 3", "Myriad Pro", sans-serif;
    color: var(--ink);
  }
  .person__name {
    font-weight: 600; font-size: 15.5px; line-height: 18px;
    color: var(--brand);
  }
  .person__title { font-size: 12.5px; line-height: 15px; }
  .person { margin-bottom: 13px; }
  .line {
    display: flex; align-items: center; gap: 6px;
    font-size: 12.5px; line-height: 17px;
  }
  .line svg { width: 10px; height: 10px; fill: var(--brand); flex: none; }
  .address { font-size: 12.5px; line-height: 16px; margin: 7px 0 10px 1px; }

  .wordmark {
    position: absolute;
    font-family: "EB Garamond", Garamond, serif;
    font-weight: 600; color: var(--brand);
    text-align: center; line-height: 1;
  }
  .wordmark--small { left: 237px; top: 98px; width: 195px; font-size: 31px; }
  .wordmark--large { left: 158px; top: 92px; width: 240px; font-size: 42px; }
  .brand-dot {
    position: absolute; left: 70px; top: 102px;
    width: 76px; height: 76px; border-radius: 50%;
    background: var(--brand);
  }
</style>
</head>
<body>
<main class="canvas">
  <section class="card card--details">
    <div class="contacts">
      <div class="person">
        <p class="person__name">Dana Pembrook</p>
        <p class="person__title">Broker</p>
        <p class="line"><svg viewBox="0 0 10 10"><path d="M2 0.5 L3.6 2.6 L2.8 3.6 Q4 6 6.4 7.2 L7.4 6.4 L9.5 8 L8.4 9.5 Q3.5 9 0.5 1.6 Z"/></svg>(555).317.6624</p>
      </div>
      <div class="person">
        <p class="person__name">Marla Pembrook</p>
        <p class="person__title">Realtor</p>
        <p class="line"><svg viewBox="0 0 10 10"><path d="M2 0.5 L3.6 2.6 L2.8 3.6 Q4 6 6.4 7.2 L7.4 6.4 L9.5 8 L8.4 9.5 Q3.5 9 0.5 1.6 Z"/></svg>(555).609.1385</p>
      </div>
      <p class="address">418B W. Calloway Ave.<br>Ashmere Vale, NW. 70913</p>
      <p class="line"><svg viewBox="0 0 10 10"><path d="M2 0.5 L3.6 2.6 L2.8 3.6 Q4 6 6.4 7.2 L7.4 6.4 L9.5 8 L8.4 9.5 Q3.5 9 0.5 1.6 Z"/></svg>(555).240.3918</p>
      <p class="line"><svg viewBox="0 0 10 10"><path d="M1 2.5 H9 V7.5 H1 Z M1.5 3 L5 5.5 L8.5 3" /></svg>pembrook@hartwellestates-demo.com</p>
      <p class="line"><svg viewBox="0 0 10 10"><circle cx="5" cy="5" r="4.5"/></svg>hartwellestates-demo.com</p>
    </div>
    <p class="wordmark wordmark--small">Hartwell<br>Estates</p>
  </section>

  <section class="card card--brand">
    <span class="brand-dot"></span>
    <p class="wordmark wordmark--large">Hartwell<br>Estates</p>
  </section>
</main>
</body>
</html>
```